Im want a website LIKE VRX's and FleetHollow.com's with product payment options like Trenzo's

I need a website LIKE VRX with a header made EXACTLY LIKE THAT OF FLEETHOLLOWS .

The front page photo should be like that of FLEETHOLLOW's webpage as well.

The name of the website will be called "M.K. (Caldera Key)".

We will be targeting ALL MARKETS in a small town in central Panama and charging businesses "listing fees" like a phone book does but also providing informational blogs, news, and other interesting activities.

THIS IS A MULTI PAGE WEBSITE

THIS IS WHERE VRX's website meets Brivelle/FleetHollow.

Once the layout is built I will tweak and modify, add information, and upload items for sale.

Here is a list of specific categories that should be listed out above the front page header image/search bar

-- Home -- News -- Travel -- Activities -- Shop & Dine -- Store -- More... --

These categories should be spread across the bottom of the page in three sections:

WHATS SO GREAT ABOUT (Caldera Key),
HAND PICKED TOURS
ACTIVITIES etc.

Also lets use www.Trenzo.example 's
"HOT DESTINATIONS"
"BEAT THE BEST PRICES IN BOQUETE"
"OCTOBERS INSIDER PICKS"
"TOP DESTINATIONS"
and spread them in four sections side-by-side near the bottom of the page.

Overall I would like to see the finished product to be something LIKE VRX's and FleetHollows.

WE NEED ONLINE PAYMENT OPTIONS LIKE BRIVELLE'S WEBSITE HAS

This will be a desktop website but should be very mobile friendly as well.

-rodmund

P.S. Good luck!

If it isn't already too late to change the website name, the name of the website should be "Caldera Key". Added Friday, October 9, 2015

What do you guys think the budget should be to win this? Added Saturday, October 10, 2015

www.palmorra.example is the most amazing simple site. Whoever can make me a replica with my specifications will win immediately!!!! Added Sunday, October 18, 2015

OMG www.palmorra.example is the bomb!So simple and elegant. Whoever can make me an EXACT REPLICA OF WWW.PALMORRA.EXAMPLE as my site with the specifications mentioned in my brief will take home the $825.00 immediately! Good luck amigos! Added Sunday, October 18, 2015

Does anybody know how to add recurring monthly billing options on this website? Added Sunday, October 18, 2015

ALL MARKETS

Product

Coded - Design and coding required

5+ page

• Coinvey payment options.
• I must be able to add and remove photos/text and video from the HTML files in the page.
• Be creative my friends, and may the odds be forever in your favor!
• I added some photos of a good layout for our page below.

```html
<!DOCTYPE html>
<html lang="en">
<head>
<meta charset="utf-8">
<title>Caldera Key</title>
<link href="https://fonts.googleapis.com/css2?family=Open+Sans:wght@400;600;700&family=Roboto:wght@300;400;500;700&display=swap" rel="stylesheet">
<style>
:root{
  --blue:#2a9fdc;
  --cyan:#2fb2c8;
  --gold:#e7b22b;
  --ink:#333c44;
  --muted:#7b858d;
  --line:#e3e7ea;
  --soft:#f3f5f6;
  --footer:#17707a;
  --footer-deep:#0f545c;
  --star:#f2a31b;
}
*{box-sizing:border-box;margin:0;padding:0}
html,body{width:1200px;height:2188px;overflow:hidden}
body{font-family:"Open Sans",Arial,sans-serif;color:var(--ink);background:#fff;font-size:13px;line-height:1.6}
.wrap{width:1024px;margin:0 auto;position:relative}
a{color:inherit;text-decoration:none}

/* top bar */
.topbar{height:32px;border-bottom:1px solid var(--line);font-size:11px;color:var(--muted)}
.topbar .wrap{display:flex;justify-content:space-between;align-items:center;height:32px}
.topbar .info{display:flex;gap:22px}
.topbar .info span{display:flex;align-items:center;gap:6px}
.topbar svg{width:11px;height:11px;fill:var(--blue)}
.topbar .prefs{display:flex;gap:18px}

/* header */
.header{height:112px}
.header .wrap{display:flex;align-items:center;justify-content:space-between;height:112px}
.brand{font-family:"Roboto",Arial,sans-serif;font-size:34px;font-weight:400;color:var(--blue);display:flex;align-items:center;gap:10px}
.brand i{width:12px;height:12px;background:var(--blue);border-radius:50%;display:block}
.nav{display:flex;align-items:center;gap:34px;font-family:"Roboto",Arial,sans-serif;font-size:13px;font-weight:500;color:var(--ink)}
.nav .active{color:var(--blue);border-bottom:2px solid var(--blue);padding-bottom:4px}
.btn-login{background:var(--blue);color:#fff;padding:10px 26px;border-radius:2px;font-size:12px}

/* hero */
.hero{height:448px;position:relative;background:linear-gradient(180deg,#6fa7cf 0%,#9cc7e0 35%,#3e7f6e 55%,#2c90b8 75%,#5cc3dd 100%)}
.hero .shade{position:absolute;top:0;bottom:0;width:88px;background:rgba(0,0,0,.35)}
.hero .shade.l{left:0}.hero .shade.r{right:0}
.hero .arrow{position:absolute;top:194px;width:40px;height:60px;display:flex;align-items:center;justify-content:center}
.hero .arrow svg{width:20px;height:36px;stroke:#fff;stroke-width:3;fill:none}
.hero .arrow.l{left:24px}.hero .arrow.r{right:24px}
.caption{position:absolute;left:150px;top:300px;color:#fff}
.caption h1{font-family:"Roboto",Arial,sans-serif;font-size:34px;font-weight:500;margin-bottom:6px;line-height:1.3}
.caption p{background:rgba(0,0,0,.45);display:inline-block;padding:6px 12px;font-size:14px;max-width:300px;line-height:1.4}

/* features */
.features{height:300px;padding-top:156px}
.features .wrap{display:flex;gap:44px}
.feature{flex:1;height:100px;color:#fff;display:flex;align-items:center;gap:18px;padding:0 22px}
.feature.blue{background:var(--blue)}.feature.cyan{background:var(--cyan)}.feature.gold{background:var(--gold)}
.feature .ic{width:52px;height:52px;border:2px solid #fff;border-radius:50%;flex:none;display:flex;align-items:center;justify-content:center}
.feature .ic svg{width:24px;height:24px;fill:none;stroke:#fff;stroke-width:2}
.feature h3{font-size:12px;font-weight:700;line-height:1.35;margin-bottom:4px}
.feature p{font-size:10px;line-height:1.4;opacity:.9}

/* welcome */
.welcome{height:208px;text-align:center}
.welcome h2{font-family:"Roboto",Arial,sans-serif;font-size:30px;font-weight:500;margin-top:56px;line-height:1.2}
.welcome h2 span{color:var(--blue)}
.welcome .rule{width:60px;height:2px;background:var(--blue);margin:10px auto 14px}
.welcome p{font-size:11px;color:var(--muted);text-align:left;line-height:1.7}

/* tourism */
.tourism{height:480px}
.sec-head{display:flex;justify-content:space-between;align-items:center;border-bottom:1px solid var(--line);padding-bottom:8px;margin-top:16px}
.sec-head h2{font-family:"Roboto",Arial,sans-serif;font-size:20px;color:var(--blue);font-weight:500}
.sec-head .arrows{display:flex;gap:8px}
.sec-head svg{width:10px;height:16px;stroke:var(--ink);stroke-width:2.5;fill:none}
.cards{display:flex;gap:42px;margin-top:14px}
.card{flex:1}
.card .photo{height:220px}
.photo.a{background:linear-gradient(180deg,#7fb6e0,#cfe3f1 45%,#4b87a9 70%,#1f5e85)}
.photo.b{background:linear-gradient(180deg,#bfe0f4,#f5efe2 50%,#d9a55e 80%,#8c6b45)}
.photo.c{background:linear-gradient(180deg,#9fcdf0,#d9ecf7 40%,#c7523b 65%,#5b4a3e)}
.card h4{font-size:15px;color:var(--blue);font-weight:700;margin-top:12px}
.rating{display:flex;align-items:center;gap:3px;margin:4px 0}
.rating svg{width:14px;height:14px;fill:var(--star)}
.rating span{font-size:11px;color:var(--muted);margin-left:8px}
.card p{font-size:11px;color:var(--muted);line-height:1.6}
.card .more{font-size:11px;color:var(--blue);margin-top:4px;display:block}

/* testimonials */
.testimonials{height:340px;background:var(--soft);text-align:center}
.testimonials h2{font-family:"Roboto",Arial,sans-serif;font-size:24px;color:var(--blue);font-weight:500;padding-top:44px;line-height:1.3}
.testimonials .rule{width:60px;height:2px;background:var(--blue);margin:8px auto 34px}
.quotes{display:flex;gap:40px;text-align:left}
.quote{flex:1;display:flex;gap:16px}
.avatar{width:76px;height:76px;border-radius:50%;background:#c9ced2;flex:none;border:3px solid #fff}
.quote p{font-size:11px;color:var(--muted);line-height:1.6}
.quote b{display:block;font-size:10px;color:var(--gold);margin-top:8px;letter-spacing:.5px}
.quote small{font-size:10px;color:var(--ink)}

/* footer */
.footer{height:228px;background:var(--footer);color:#d8ecee}
.footer .wrap{display:flex;gap:40px;padding-top:28px}
.fcol{flex:1}
.fcol h5{font-size:13px;color:#fff;font-weight:700;margin-bottom:12px;letter-spacing:.5px}
.fcol p,.fcol li{font-size:11px;line-height:1.7}
.fcol ul{list-style:none}
.fcol li::before{content:"›";margin-right:6px}
.btn-gold{display:inline-block;background:var(--gold);color:#fff;font-size:10px;font-weight:700;padding:7px 16px;margin-top:12px}
.subscribe{display:flex;margin-top:12px}
.subscribe span{flex:1;background:#fff;color:#999;font-size:10px;padding:7px 8px}
.subscribe b{background:var(--gold);color:#fff;font-size:10px;padding:7px 12px}
.social{display:flex;gap:10px;margin-top:14px}
.social i{width:26px;height:26px;border-radius:50%;background:rgba(255,255,255,.2);display:block}
.bottom{height:40px;background:var(--footer-deep);color:#c4dfe2;font-size:10px;text-align:center;line-height:40px}
</style>
</head>
<body>

<div class="topbar">
  <div class="wrap">
    <div class="info">
      <span><svg viewBox="0 0 24 24"><path d="M6.6 10.8a15 15 0 0 0 6.6 6.6l2.2-2.2a1 1 0 0 1 1-.25 11 11 0 0 0 3.6.6 1 1 0 0 1 1 1V20a1 1 0 0 1-1 1A17 17 0 0 1 3 4a1 1 0 0 1 1-1h3.5a1 1 0 0 1 1 1 11 11 0 0 0 .6 3.6 1 1 0 0 1-.25 1z"/></svg>+1 (507) 555 0134</span>
      <span><svg viewBox="0 0 24 24"><path d="M12 2a7 7 0 0 0-7 7c0 5 7 13 7 13s7-8 7-13a7 7 0 0 0-7-7zm0 9.5A2.5 2.5 0 1 1 12 6.5a2.5 2.5 0 0 1 0 5z"/></svg>Find our Address</span>
      <span><svg viewBox="0 0 24 24"><path d="M2 5h20v14H2zm2 2v.5l8 5 8-5V7z"/></svg>hello@calderakey.example</span>
    </div>
    <div class="prefs"><span>USD ▾</span><span>English ▾</span></div>
  </div>
</div>

<header class="header">
  <div class="wrap">
    <div class="brand"><i></i>Caldera Key</div>
    <nav class="nav">
      <a class="active">HOME</a><a>TOURS</a><a>ABOUT US</a><a>BOOKING</a><a>CONTACT US</a>
      <a class="btn-login">LOGIN</a>
    </nav>
  </div>
</header>

<section class="hero" role="img" aria-label="Resort pool lined with palm trees under a blue sky">
  <div class="shade l"></div><div class="shade r"></div>
  <div class="arrow l"><svg viewBox="0 0 20 36"><path d="M18 2 2 18l16 16"/></svg></div>
  <div class="arrow r"><svg viewBox="0 0 20 36"><path d="M2 2l16 16L2 34"/></svg></div>
  <div class="caption">
    <h1>Caldera Key</h1>
    <p>We will be bringing tourism to a small town in central Panama</p>
  </div>
</section>

<section class="features">
  <div class="wrap">
    <div class="feature blue">
      <div class="ic"><svg viewBox="0 0 24 24"><circle cx="12" cy="12" r="9"/><path d="M12 3v18M3 12h18"/></svg></div>
      <div><h3>ROLLING<br>GUIDED TOURS</h3><p>Local guides show you the best of the island each day.</p></div>
    </div>
    <div class="feature cyan">
      <div class="ic"><svg viewBox="0 0 24 24"><path d="M4 20V9l8-5 8 5v11zM10 20v-6h4v6"/></svg></div>
      <div><h3>CALDERA KEY<br>HOTEL RENTALS</h3><p>Comfortable rooms and villas close to the beach and town.</p></div>
    </div>
    <div class="feature gold">
      <div class="ic"><svg viewBox="0 0 24 24"><circle cx="7" cy="12" r="3"/><circle cx="17" cy="12" r="3"/><path d="M3 20c1-3 3-4 4-4s3 1 4 4M13 20c1-3 3-4 4-4s3 1 4 4"/></svg></div>
      <div><h3>BRING ALONG IN<br>MAIN FOOD PRICE</h3><p>Meals for the whole group included at one simple price.</p></div>
    </div>
  </div>
</section>

<section class="welcome">
  <div class="wrap">
    <h2>WELCOME TO <span>CALDERA KEY</span></h2>
    <div class="rule"></div>
    <p>Lorem Ipsum has been the industry's standard dummy text ever since the 1500s, when an unknown printer took a galley of type and scrambled it to make a type specimen book. It has survived not only five centuries, but also the leap into electronic typesetting, remaining essentially unchanged. It was popularised in the 1960s with the release of sheets containing passages, and more recently with desktop publishing software including versions of it. Lorem Ipsum has been the industry's standard dummy text ever since the 1500s, when an unknown printer took a galley of type and scrambled it to make a type specimen book for visitors.</p>
  </div>
</section>

<section class="tourism">
  <div class="wrap">
    <div class="sec-head">
      <h2>TOURISM</h2>
      <div class="arrows"><svg viewBox="0 0 10 16"><path d="M8 2 2 8l6 6"/></svg><svg viewBox="0 0 10 16"><path d="M2 2l6 6-6 6"/></svg></div>
    </div>
    <div class="cards">
      <article class="card">
        <div class="photo a" role="img" aria-label="City skyline across the water"></div>
        <h4>Neque porro quisquam est</h4>
        <div class="rating"><svg viewBox="0 0 24 24"><path d="m12 2 3 7h7l-5.5 4.5 2 7.5-6.5-4.5L5.5 21l2-7.5L2 9h7z"/></svg><svg viewBox="0 0 24 24"><path d="m12 2 3 7h7l-5.5 4.5 2 7.5-6.5-4.5L5.5 21l2-7.5L2 9h7z"/></svg><svg viewBox="0 0 24 24"><path d="m12 2 3 7h7l-5.5 4.5 2 7.5-6.5-4.5L5.5 21l2-7.5L2 9h7z"/></svg><svg viewBox="0 0 24 24"><path d="m12 2 3 7h7l-5.5 4.5 2 7.5-6.5-4.5L5.5 21l2-7.5L2 9h7z"/></svg><svg viewBox="0 0 24 24"><path d="m12 2 3 7h7l-5.5 4.5 2 7.5-6.5-4.5L5.5 21l2-7.5L2 9h7z"/></svg><span>102 Reviews</span></div>
        <p>Lorem Ipsum has been the industry's standard dummy text ever since the 1500s, when an unknown printer took a galley of type and scrambled it to make a book.</p>
        <a class="more">Read More »</a>
      </article>
      <article class="card">
        <div class="photo b" role="img" aria-label="World landmarks gathered on a globe"></div>
        <h4>Neque porro quisquam est</h4>
        <div class="rating"><svg viewBox="0 0 24 24"><path d="m12 2 3 7h7l-5.5 4.5 2 7.5-6.5-4.5L5.5 21l2-7.5L2 9h7z"/></svg><svg viewBox="0 0 24 24"><path d="m12 2 3 7h7l-5.5 4.5 2 7.5-6.5-4.5L5.5 21l2-7.5L2 9h7z"/></svg><svg viewBox="0 0 24 24"><path d="m12 2 3 7h7l-5.5 4.5 2 7.5-6.5-4.5L5.5 21l2-7.5L2 9h7z"/></svg><svg viewBox="0 0 24 24"><path d="m12 2 3 7h7l-5.5 4.5 2 7.5-6.5-4.5L5.5 21l2-7.5L2 9h7z"/></svg><svg viewBox="0 0 24 24"><path d="m12 2 3 7h7l-5.5 4.5 2 7.5-6.5-4.5L5.5 21l2-7.5L2 9h7z"/></svg><span>102 Reviews</span></div>
        <p>Lorem Ipsum has been the industry's standard dummy text ever since the 1500s, when an unknown printer took a galley of type and scrambled it to make a book.</p>
        <a class="more">Read More »</a>
      </article>
      <article class="card">
        <div class="photo c" role="img" aria-label="Traveller with a backpack on a city street"></div>
        <h4>Neque porro quisquam est</h4>
        <div class="rating"><svg viewBox="0 0 24 24"><path d="m12 2 3 7h7l-5.5 4.5 2 7.5-6.5-4.5L5.5 21l2-7.5L2 9h7z"/></svg><svg viewBox="0 0 24 24"><path d="m12 2 3 7h7l-5.5 4.5 2 7.5-6.5-4.5L5.5 21l2-7.5L2 9h7z"/></svg><svg viewBox="0 0 24 24"><path d="m12 2 3 7h7l-5.5 4.5 2 7.5-6.5-4.5L5.5 21l2-7.5L2 9h7z"/></svg><svg viewBox="0 0 24 24"><path d="m12 2 3 7h7l-5.5 4.5 2 7.5-6.5-4.5L5.5 21l2-7.5L2 9h7z"/></svg><svg viewBox="0 0 24 24"><path d="m12 2 3 7h7l-5.5 4.5 2 7.5-6.5-4.5L5.5 21l2-7.5L2 9h7z"/></svg><span>102 Reviews</span></div>
        <p>Lorem Ipsum has been the industry's standard dummy text ever since the 1500s, when an unknown printer took a galley of type and scrambled it to make a book.</p>
        <a class="more">Read More »</a>
      </article>
    </div>
  </div>
</section>

<section class="testimonials">
  <div class="wrap">
    <h2>TESTIMONIALS</h2>
    <div class="rule"></div>
    <div class="quotes">
      <div class="quote"><div class="avatar" role="img" aria-label="Guest portrait"></div><div><p>"Lorem ipsum is simply dummy text of the printing and typesetting industry. It has been the standard for years."</p><b>LENA FARROW</b><small>Marketing Executive</small></div></div>
      <div class="quote"><div class="avatar" role="img" aria-label="Guest portrait"></div><div><p>"Lorem ipsum is simply dummy text of the printing and typesetting industry. It has been the standard for years."</p><b>ODILE MARCHETTI</b><small>Marketing Executive</small></div></div>
      <div class="quote"><div class="avatar" role="img" aria-label="Guest portrait"></div><div><p>"Lorem ipsum is simply dummy text of the printing and typesetting industry. It has been the standard for years."</p><b>TOBIAS WRENFIELD</b><small>Marketing Executive</small></div></div>
    </div>
  </div>
</section>

<footer class="footer">
  <div class="wrap">
    <div class="fcol">
      <h5>MILEAGE PROGRAM</h5>
      <p>Lorem Ipsum has been the industry's standard dummy text ever since the 1500s, when an unknown printer took a galley of type and scrambled it.</p>
      <a class="btn-gold">READ MORE</a>
    </div>
    <div class="fcol">
      <h5>LINKS</h5>
      <ul><li>Customer Support</li><li>Documentation</li><li>Advertise</li><li>General Help</li><li>Affiliations</li></ul>
    </div>
    <div class="fcol">
      <h5>GET IN TOUCH</h5>
      <p>Address : 12 Harbor Lane,<br>Caldera Key, Panama</p>
      <p>Phone : +1 (507) 555 0134</p>
      <p>Email : hello@calderakey.example</p>
    </div>
    <div class="fcol">
      <h5>NEWSLETTER</h5>
      <p>Join our newsletter to hear about new tours and local deals.</p>
      <div class="subscribe"><span>Enter your email</span><b>SUBSCRIBE</b></div>
      <div class="social"><i></i><i></i><i></i><i></i></div>
    </div>
  </div>
</footer>
<div class="bottom">Copyright © 2015 · All Rights Reserved · Caldera Key</div>

</body>
</html>
```